BildeVOLD buisnesscard

Hey :) I need a modern buisnesscard for my company BildeVOLD
It most have:
Dagligleder og Fotograf: Henrik Audun Strandvik

Mob: +4791264085
Epost: post@bildevold.example
Adresse: Kvernbakken9, 6040 Langevåg

Facbook and instagram logo with text BildeVOLD

BildeVOLD logo

It Company

```html
<!DOCTYPE html>
<html lang="no">
<head>
<meta charset="utf-8">
<title>BildeVOLD – visittkort</title>
<link href="https://fonts.googleapis.com/css2?family=Inter:wght@400;500;600&display=swap" rel="stylesheet">
<style>
  :root {
    --page: #ffffff;
    --purple: #4a0052;
    --purple-band: #570063;
    --purple-deep: #500059;
    --blue: #042a86;
    --blue-soft: #0a34a0;
    --ink-light: #e8e6ee;
    --ink-muted: #d9d3de;
  }
  * { box-sizing: border-box; margin: 0; padding: 0; }
  html, body { width: 1200px; height: 850px; overflow: hidden; background: var(--page); }
  body { position: relative; font-family: "Inter", sans-serif; color: var(--ink-light); }

  .card {
    position: absolute; top: 287px; width: 480px; height: 275px; overflow: hidden;
  }
  .card--front { left: 109px; background: var(--purple); }
  .card--back {
    left: 611px;
    background: linear-gradient(110deg, var(--blue) 0%, var(--blue) 55%, var(--blue-soft) 100%);
  }
  .card__bands { position: absolute; inset: 0; }

  .brand {
    position: absolute; left: 0; right: 0; text-align: center;
    font-weight: 600; color: var(--ink-light); letter-spacing: 0.2px;
  }
  .brand__square {
    display: inline-block; background: var(--ink-light); vertical-align: middle;
  }
  .card--front .brand { top: 52px; font-size: 21px; }
  .card--front .brand__square { width: 14px; height: 14px; margin-right: 8px; margin-top: -3px; }
  .card--back .brand { top: 112px; font-size: 38px; }
  .card--back .brand__square { width: 26px; height: 26px; margin-right: 12px; margin-top: -5px; }

  .person {
    position: absolute; top: 124px; left: 0; right: 0; text-align: center;
  }
  .person__name { font-size: 25px; font-weight: 400; line-height: 1.2; }
  .person__role { margin-top: 6px; font-size: 16px; color: var(--ink-muted); }

  .contacts {
    position: absolute; top: 234px; left: 12px; right: 12px;
    list-style: none;
    display: flex; justify-content: center; gap: 16px;
    font-size: 11px; color: var(--ink-muted);
  }
  .contacts__item, .social__item { display: flex; align-items: center; gap: 5px; white-space: nowrap; }
  .contacts svg { width: 9px; height: 9px; fill: var(--ink-muted); flex: none; }

  .social {
    position: absolute; top: 233px; left: 0; right: 0;
    display: flex; justify-content: center; gap: 30px; font-size: 12px; color: var(--ink-muted);
  }
  .social__dot { width: 10px; height: 10px; border-radius: 50%; background: var(--ink-muted); }
</style>
</head>
<body>

  <section class="card card--front" aria-label="Forside">
    <svg class="card__bands" viewBox="0 0 480 275" aria-hidden="true">
      <polygon points="0,0 22,0 290,275 0,275" fill="var(--purple-band)"/>
      <polygon points="0,75 200,275 0,275" fill="var(--purple-deep)"/>
      <polygon points="48,205 70,205 140,275 48,275" fill="var(--purple-deep)"/>
    </svg>

    <div class="brand"><span class="brand__square"></span>BildeVOLD</div>

    <div class="person">
      <h1 class="person__name">Henrik Audun Strandvik</h1>
      <p class="person__role">Dagligleder og Fotograf</p>
    </div>

    <ul class="contacts">
      <li class="contacts__item">
        <svg viewBox="0 0 10 10"><path d="M2 0.5 L3.6 2.6 L2.8 3.6 Q4 6 6.4 7.2 L7.4 6.4 L9.5 8 L8.4 9.5 Q3.5 9 0.5 1.6 Z"/></svg>
        +4791264085
      </li>
      <li class="contacts__item">
        <svg viewBox="0 0 12 9" style="width:11px"><path d="M0 0 H12 V9 H0 Z M1 1 L6 5 L11 1 Z" fill-rule="evenodd"/></svg>
        post@bildevold.example
      </li>
      <li class="contacts__item">
        <svg viewBox="0 0 10 10"><path d="M10 0 L0 4.2 L4.6 5.4 L5.8 10 Z"/></svg>
        Kvernbakken9, 6040 Langevåg
      </li>
    </ul>
  </section>

  <section class="card card--back" aria-label="Bakside">
    <div class="brand"><span class="brand__square"></span>BildeVOLD</div>

    <div class="social">
      <span class="social__item"><span class="social__dot"></span>BildeVOLD</span>
      <span class="social__item"><span class="social__dot"></span>BildeVOLD</span>
    </div>
  </section>

</body>
</html>
```